Verpackungen für  Lebensmittelmanufaktur
Verpackungen für Lebensmittelmanufaktur
Henrike war super und unser Feedback perfekt umgesetzt. es war und ist eine tolle Erfahrung mit ihr zu arbeiten. Gerne und jederzeit wieder! Brotolin
Zielgruppe
Wir sind eine kleine Lebensmittelmanufaktur die ihr eigenes Granola herausbringen möchte. Dieses Projekt ist ein Test, weil dieses Produkt neu für uns ist und wir noch überhaupt nicht wissen, ob es sich verkaufen wird. Deshalb ist unser Budget auch begrenzt. Wenn es anläuft wird es mehrere Varianten geben, diese werden dann auch hier designed und der Gewinner diese Projekts wird hier ganz vorne mit dabei sein. Die Zielgruppe sind Menschen, die neugierig auf neues Essen sind. Im Alter zwischen 20 und 45 Jahren.
Aufgabenstellung
Für unsere Granola/ Müsli Verpackung brauchen wir ein Frontbild. Der Name und der Sloagen stehen fest.
Name: Morgenflug Müsli/ Granola
Slogan: Bringt dich auf Lichtgeschwindigkeit
Geschmacksrichtung: Pekan & Zimt
Art und Weise: Crunchy & Crispy
Eigenschaft: Glutenfrei & ohne zugesetzten Zucker
Die Idee ist, es mit dem Weltraum zu verbinden, da es schwerelos macht und so der Tag leicht startet.
Für die Grafiken in der Datei granola_gestaltwerkstatt-netz.ai haben wir alle Rechte. Uns fehlt hier noch die Tiefe des Weltraums und das notwendige Know-how. Weiter kommen wir ohne Hilfe nicht :-)
Hier kommst du ins Spiel.
Wir freuen uns auf deinen Vorschlag
Wenn du Bilder vorschlägst, bevorzugen wir die von Quorvix Vorlagen.
Bei den Farben sind wir offen, das waren nur erste Ideen.
Wie gesagt, reicht uns nur das Frontbild. Die restlichen Angaben fügen wir später selbst ein.
Wir benötigen also nicht ein komplettes Verpackungsdesign, sondern nur die Front.
Die Frontmaße sind 190 x 215 mm
Wir erwarten Illustrator, oder In-Design Daten.
Wir haben noch ein paar Inspirationen beigefügt.

```html
<!DOCTYPE html>
<html lang="de">
<head>
<meta charset="utf-8">
<title>Morgenflug Müsli – Frontetikett</title>
<link rel="stylesheet" href="https://fonts.googleapis.com/css2?family=Montserrat:wght@800&family=Saira+Condensed:ital,wght@1,400;1,500&family=Exo+2:wght@400&display=swap">
<style>
  :root {
    --page-bg: #ffffff;
    --label-bg: #2c1210;
    --orange: #f0a030;
    --moon: #e9a945;
    --cream: #efe6dc;
    --ice: #a9e4ec;
    --white: #ffffff;
    --astro-a: #d98a3a;
    --astro-b: #6d9fb2;
  }
  * { margin: 0; padding: 0; box-sizing: border-box; }
  html, body { width: 1200px; height: 1200px; overflow: hidden; background: var(--page-bg); }
  .label {
    position: absolute; left: 50px; top: 265px; width: 1100px; height: 670px;
    background:
      radial-gradient(ellipse 380px 220px at 330px 420px, rgba(110,42,36,.55), transparent 70%),
      radial-gradient(ellipse 300px 200px at 760px 360px, rgba(90,36,32,.35), transparent 70%),
      var(--label-bg);
    overflow: hidden;
  }
  .orbit { position: absolute; inset: 0; width: 1100px; height: 670px; }
  .astronaut-art {
    position: absolute; left: 630px; top: 130px; width: 380px; height: 430px;
    background: radial-gradient(ellipse closest-side, var(--astro-b) 0%, var(--astro-a) 45%, rgba(217,138,58,.35) 75%, rgba(217,138,58,0) 100%);
    opacity: .85;
  }
  .moon-art {
    position: absolute; left: 888px; top: 140px; width: 126px; height: 126px;
    border-radius: 50%;
    background: radial-gradient(circle at 40% 40%, #f2bb5c, var(--moon) 60%, #c98a2e);
  }
  .brand-name {
    position: absolute; left: 532px; top: 26px;
    font-family: "Montserrat", sans-serif; font-weight: 800; font-size: 62px;
    color: var(--cream); letter-spacing: -1px; line-height: 1;
  }
  .variety {
    position: absolute; font-family: "Saira Condensed", sans-serif;
    font-style: italic; color: var(--cream); line-height: 1;
  }
  .variety--granola { left: 880px; top: 104px; font-size: 30px; }
  .variety--muesli { left: 752px; top: 130px; font-size: 46px; }
  .variety--flavour { left: 782px; top: 172px; font-size: 30px; }
  .slogan {
    position: absolute; left: 574px; width: 410px; text-align: center;
    font-family: "Exo 2", sans-serif; color: var(--ice); line-height: 1;
    letter-spacing: 2px;
  }
  .slogan--top { top: 512px; font-size: 31px; }
  .slogan--bottom { top: 568px; font-size: 33px; }
  .texture {
    position: absolute; left: 574px; top: 624px; width: 410px; text-align: center;
    font-family: "Saira Condensed", sans-serif; font-style: italic; font-weight: 500;
    font-size: 25px; color: var(--white); line-height: 1;
  }
</style>
</head>
<body>
  <main class="label">
    <svg class="orbit" viewBox="0 0 1100 670" aria-hidden="true">
      <defs>
        <linearGradient id="shooting-star" x1="630" y1="175" x2="510" y2="295" gradientUnits="userSpaceOnUse">
          <stop offset="0" stop-color="#ffffff" stop-opacity="0"/>
          <stop offset="1" stop-color="#ffffff" stop-opacity="1"/>
        </linearGradient>
      </defs>
      <g fill="#ffffff" opacity=".7">
        <circle cx="70" cy="120" r="1.5"/><circle cx="210" cy="60" r="1.2"/>
        <circle cx="300" cy="200" r="1.5"/><circle cx="140" cy="330" r="1.2"/>
        <circle cx="420" cy="40" r="1.8"/><circle cx="470" cy="470" r="1.2"/>
        <circle cx="260" cy="560" r="1.5"/><circle cx="1040" cy="90" r="1.5"/>
        <circle cx="1060" cy="420" r="1.8"/><circle cx="990" cy="560" r="1.2"/>
        <circle cx="560" cy="630" r="1.5"/><circle cx="80" cy="600" r="1.2"/>
      </g>
      <path d="M 560 116 A 222 222 0 1 0 640 543" fill="none" stroke="var(--orange)" stroke-width="3"/>
      <line x1="630" y1="175" x2="510" y2="295" stroke="url(#shooting-star)" stroke-width="2.5"/>
      <circle cx="510" cy="295" r="4" fill="#ffffff"/>
    </svg>

    <div class="astronaut-art" role="img" aria-label="Illustration: Astronaut springt mit Skateboard durch den Weltraum, umgeben von orangem Farbspritzer"></div>
    <div class="moon-art" role="img" aria-label="Illustration: oranger Mond mit gezeichneten Zimtstangen, Sternanis und Pekannüssen"></div>

    <h1 class="brand-name">Morgenflug</h1>
    <p class="variety variety--granola">granola</p>
    <p class="variety variety--muesli">müsli</p>
    <p class="variety variety--flavour">pekan+zimt</p>

    <p class="slogan slogan--top">BRINGT DICH AUF</p>
    <p class="slogan slogan--bottom">LICHTGESCHWINDIGKEIT</p>
    <p class="texture">Crunchy+Crispy</p>
  </main>
</body>
</html>
```